Ridgeline Orchards Organic Cherry POS card 7x11

We are wanting to create a one-sided 7 x 11 organic cherry card that is eye catching and informative.This should be clear and easy to read and not cluttered. We use these cards as a display in grocery stores, demo stands, and other events to market Organic Ridgeline Sweet Orchards. We have a few facts that we would like displayed on the card (see attachment).

Target Market(s)

Consumers

Industry/Entity Type

Agriculture

Requirements
Must have
• Natural color palettes
• Easy to read
• Ridgeline Orchards
Nice to have
• Unique, realistic cherry design

```html
<!DOCTYPE html>
<html lang="en">
<head>
<meta charset="utf-8">
<title>Ridgeline Orchards – Organic Cherry Card</title>
<link rel="stylesheet" href="https://fonts.googleapis.com/css2?family=Josefin+Sans:wght@600&family=Dancing+Script:wght@600&display=swap">
<style>
  :root {
    --page: #ffffff;
    --cherry-pink: #f07176;
    --wine: #651d2b;
    --ink: #3a2326;
    --cream: #ffffff;
    --fruit-deep: #5a0f1c;
    --fruit-mid: #8e1c2e;
  }
  * { margin: 0; padding: 0; box-sizing: border-box; }
  html, body {
    width: 1200px; height: 880px;
    overflow: hidden;
    background: var(--page);
  }
  .card {
    position: absolute;
    left: 0; top: 58px;
    width: 1200px; height: 764px;
    background: var(--cherry-pink);
    overflow: hidden;
  }
  .card__band {
    position: absolute; inset: 0;
    width: 1200px; height: 764px;
    z-index: 0;
  }
  .cherry-photo {
    position: absolute;
    left: 340px; top: 306px;
    width: 390px; height: 224px;
    border-radius: 50%;
    background: radial-gradient(ellipse at 50% 50%, var(--fruit-mid) 0%, var(--fruit-deep) 70%);
    z-index: 1;
  }
  .fact {
    position: absolute;
    font-family: "Josefin Sans", sans-serif;
    font-weight: 600;
    color: var(--ink);
    text-transform: uppercase;
    z-index: 2;
  }
  .fact--share {
    left: 36px; top: 38px;
    font-size: 30px;
    line-height: 58px;
    letter-spacing: 0.3em;
  }
  .fact--state {
    right: 40px; top: 392px;
    font-size: 31px;
    line-height: 44px;
    letter-spacing: 0.33em;
    text-align: right;
  }
  .benefits {
    position: absolute;
    left: 0; top: 0;
    width: 1200px; height: 764px;
    z-index: 2;
  }
  .benefits__list {
    position: absolute;
    left: 700px; top: 40px;
    width: 400px;
    list-style: none;
    font-family: "Dancing Script", cursive;
    font-weight: 600;
    font-size: 26px;
    color: var(--cream);
    text-align: center;
    line-height: 44px;
    z-index: 3;
  }
  .brand {
    position: absolute;
    left: 30px; top: 618px;
    display: flex; align-items: center; gap: 22px;
    z-index: 2;
  }
  .brand__dot {
    width: 62px; height: 62px;
    border: 3px solid var(--cream);
    border-radius: 50%;
  }
  .brand__name {
    font-family: "Josefin Sans", sans-serif;
    font-weight: 600;
    font-size: 44px;
    color: var(--cream);
    letter-spacing: 0.04em;
  }
</style>
</head>
<body>
  <main class="card">
    <svg class="card__band" viewBox="0 0 1200 764" aria-hidden="true">
      <polygon points="0,506 1200,698 1200,764 0,764" fill="var(--wine)"/>
    </svg>

    <div class="cherry-photo" role="img" aria-label="Photo of two dark red cherries with stems twisted into a heart"></div>

    <p class="fact fact--share">Organic<br>Ridgeline Orchards<br>make up 1/3<br>of the nation's<br>production.</p>

    <svg class="benefits" viewBox="0 0 1200 764" aria-hidden="true">
      <circle cx="918" cy="188" r="150" fill="none" stroke="var(--cream)" stroke-opacity="0.55" stroke-width="3"/>
      <path d="M796 242 Q750 252 722 276" fill="none" stroke="var(--cream)" stroke-width="2.5" stroke-linecap="round"/>
      <path d="M722 262 L720 278 L736 279" fill="none" stroke="var(--cream)" stroke-width="2.5" stroke-linecap="round" stroke-linejoin="round"/>
    </svg>
    <ul class="benefits__list">
      <li>Health benefits:</li>
      <li>fat free</li>
      <li>source of vitamin C</li>
      <li>a natural anti-inflammatory</li>
      <li>source of potassium</li>
      <li>source of melatonin</li>
    </ul>

    <p class="fact fact--state">Washington state<br>is the nation's<br>largest producer<br>of organic<br>cherries.</p>

    <div class="brand">
      <span class="brand__dot"></span>
      <span class="brand__name">Ridgeline Orchards</span>
    </div>
  </main>
</body>
</html>
```